Label design - Superfood blend

We are a family owned nutrition company with big ambitions. Our goal is to develop a range of 100% natural supplements for women, inspired by nature & modern technology that helps them meet their nutritional needs while nourishing them from within. All our products are junk free because we believe that that’s how nature intended it. We also produce products through a sustainable process and only use biodegradable packaging for our products (See link - https://www.loamwrap.org.uk/biodegradable-stand-pouch-250g-kraft)

Our brand style is modern and minimalist. This same style will be reflected in our social media, website and we want it to be represented through the label designs for our product packaging.

We want some creative designers to design a label that is true to our style (See attached packaging brief with designs we like) and displays our values of Premium, High Quality, Organic Real Food supplements focused on women. I have provided examples in the attached brief, but please only use as inspiration, I dont want any of them to be copied (sorry have had my fingers burnt already !)
Updates

Hello all, Please note this design is for a LABEL and not the whole package. We will have a 500gm biodegradable brown package, and we will have a label (which is what this project is about) that will be stuck on the front. The size of the label will be a rectangle (unless you come up with a new shape) in the size 20cm * 15cm. Please do not submit designs for the WHOLE from of the package, as we dont intend to have printed packages. Regards

Hello all, I have added a new logo version to the attachments, could you please also try that version. Could you also please look at the new sliders. We are only looking for a minimlaist theme. If you dont know what that means, please do feel free to ask, I would be happy to supply examples. Minimalist designs, means clean, modern, upmarket, elegant designs. It does not use too many colors and mostly sticks to a combination of black and white with colors used sparingly. See some below for your reference anyway. https://www.pitchloft.co.uk/design/13359317 https://www.pitchloft.co.uk/design/17270649 https://www.pitchloft.co.uk/design/12584145 https://www.pitchloft.co.uk/design/12367479 https://www.snapquilt.com/search/pins/?q=minimalist%20label%20design&rs=rs&eq=&etslf=2809&term_meta[]=minimalist%7Crecentsearch%7Cundefined&term_meta[]=label%7Crecentsearch%7Cundefined&term_meta[]=design%7Crecentsearch%7Cundefined Regards

Target Market(s)

The target market is women between the age 25 to 45, based in UK (mostly based in larger cities in UK). They are typically middle class or higher and would be in demanding jobs and social lives, that requires for them to meet their nutrition needs in convenient, easy to take forms. The women would also be socially conscious and sensitive to issues like women's rights, environmental issues, healthy food, organic food and sustainability etc. I have a much more detailed customer avatar if required

Font styles to use
Serif
Sans Serif
Decorative
Script

Colors
e8e8e8
474747
1b1b1b
add136

Requirements
Must have
• The label, should look minimalist and modern, throw in some out of the box creativity and we have a winner. Creativity will definitely be of importance. Our packaging is a biodegradable brown paper stand up pouch (Example link in product description). So to make it standout from other colorful packaging - being creative would definitely help.
• Please use the color schemes provided in the brief (See attachments). But if you want to experiment I would be open to it, as long as they are still minimalist and does not stray very far from the color given in the brief :)

```html
<!DOCTYPE html>
<html lang="en">
<head>
<meta charset="utf-8">
<title>Veridano Label Range</title>
<link rel="stylesheet" href="https://fonts.googleapis.com/css2?family=Poppins:wght@300;400;500;600;700&display=swap">
<style>
  :root{
    --backdrop:#e8e8ea;
    --paper:#ffffff;
    --ink:#111111;
    --rule:#1b1b1b;
    --mulberry:#b5646c;
    --goji:#e8343f;
    --goji-soft:#d4696d;
    --badge:#474747;
  }
  *{margin:0;padding:0;box-sizing:border-box}
  html,body{width:800px;height:1200px;overflow:hidden;background:var(--backdrop)}
  body{position:relative;font-family:'Poppins',sans-serif;color:var(--ink)}
  .label{position:absolute;width:250px;height:340px;background:var(--paper);border-radius:9px;overflow:hidden}
  .col-left{left:136px}.col-right{left:414px}
  .row-1{top:58px}.row-2{top:431px}.row-3{top:804px}

  .brand{position:absolute;left:18px;top:12px;height:284px;width:36px;
    writing-mode:vertical-rl;transform:rotate(180deg);
    font-weight:400;font-size:31px;letter-spacing:10px;line-height:36px;text-align:center;color:var(--ink)}

  .title{position:absolute;left:78px;top:100px;font-weight:700;font-size:33px;line-height:1.1;letter-spacing:-0.5px;white-space:nowrap}
  .title.outlined{color:transparent;-webkit-text-stroke:0.8px var(--ink)}
  .subtitle{position:absolute;left:78px;top:143px;font-weight:600;font-size:20px;line-height:1.1;white-space:nowrap}
  .is-mulberry{color:var(--mulberry)}
  .is-goji{color:var(--goji)}
  .is-goji-soft{color:var(--goji-soft)}

  .divider{position:absolute;left:78px;top:179px;width:149px;height:1px;background:var(--rule)}
  .blurb{position:absolute;left:78px;top:184px;width:150px;font-size:5.4px;font-weight:500;line-height:1.45;letter-spacing:-0.1px}
  .ingredients{position:absolute;left:78px;top:216px;list-style:none;font-size:8.4px;font-weight:300;line-height:16px}
  .ingredients li::before{content:"\2665";font-size:7px;margin-right:4px;vertical-align:1px}
  .claim{position:absolute;left:81px;top:286px;font-size:5.2px;font-weight:700;letter-spacing:0.1px}

  .footer-rule{position:absolute;left:0;right:0;top:302px;height:1px;background:var(--rule)}
  .badge{position:absolute;top:309px;width:24px;height:24px;border-radius:50%;border:1.4px solid var(--badge)}
  .badge-organic{left:27px}
  .badge-vegan{left:195px;width:27px;height:27px;top:307px}
</style>
</head>
<body>

  <section class="label col-left row-1">
    <div class="brand">VERIDANO</div>
    <div class="title">PLUCKY</div>
    <div class="subtitle is-mulberry">MULBERRIES</div>
    <div class="divider"></div>
    <p class="blurb">Plump organic mulberries coated in smooth raw chocolate for a wholesome lift wherever you go</p>
    <ul class="ingredients"><li>Organic Mulberries</li><li>Smooth Raw Chocolate</li></ul>
    <p class="claim">NO ARTIFICIAL ADDITIVES OR PRESERVATIVES</p>
    <div class="footer-rule"></div>
    <div class="badge badge-organic" role="img" aria-label="Organic certification badge"></div>
    <div class="badge badge-vegan" role="img" aria-label="Vegan certification badge"></div>
  </section>

  <section class="label col-right row-1">
    <div class="brand">VERIDANO</div>
    <div class="title">ZIPPY</div>
    <div class="subtitle is-goji">GOJI</div>
    <div class="divider"></div>
    <p class="blurb">Wonderfully nourishing organic goji berries wrapped in smooth raw chocolate for a bright afternoon lift</p>
    <ul class="ingredients"><li>Organic Goji Berries</li><li>Smooth Raw Chocolate</li></ul>
    <p class="claim">NO ARTIFICIAL ADDITIVES OR PRESERVATIVES</p>
    <div class="footer-rule"></div>
    <div class="badge badge-organic" role="img" aria-label="Organic certification badge"></div>
    <div class="badge badge-vegan" role="img" aria-label="Vegan certification badge"></div>
  </section>

  <section class="label col-left row-2">
    <div class="brand">VERIDANO</div>
    <div class="title outlined">PLUCKY</div>
    <div class="subtitle is-mulberry">MULBERRIES</div>
    <div class="divider"></div>
    <p class="blurb">Plump organic mulberries coated in smooth raw chocolate for a wholesome lift wherever you go</p>
    <ul class="ingredients"><li>Organic Mulberries</li><li>Smooth Raw Chocolate</li></ul>
    <p class="claim">NO ARTIFICIAL ADDITIVES OR PRESERVATIVES</p>
    <div class="footer-rule"></div>
    <div class="badge badge-organic" role="img" aria-label="Organic certification badge"></div>
    <div class="badge badge-vegan" role="img" aria-label="Vegan certification badge"></div>
  </section>

  <section class="label col-right row-2">
    <div class="brand">VERIDANO</div>
    <div class="title outlined">ZIPPY</div>
    <div class="subtitle is-goji">GOJI</div>
    <div class="divider"></div>
    <p class="blurb">Wonderfully nourishing organic goji berries wrapped in smooth raw chocolate for a bright afternoon lift</p>
    <ul class="ingredients"><li>Organic Goji Berries</li><li>Smooth Raw Chocolate</li></ul>
    <p class="claim">NO ARTIFICIAL ADDITIVES OR PRESERVATIVES</p>
    <div class="footer-rule"></div>
    <div class="badge badge-organic" role="img" aria-label="Organic certification badge"></div>
    <div class="badge badge-vegan" role="img" aria-label="Vegan certification badge"></div>
  </section>

  <section class="label col-left row-3">
    <div class="brand">VERIDANO</div>
    <div class="title">PLUCKY</div>
    <div class="subtitle is-mulberry">MULBERRIES</div>
    <div class="divider"></div>
    <p class="blurb">Plump organic mulberries coated in smooth raw chocolate for a wholesome lift wherever you go</p>
    <ul class="ingredients"><li>Organic Mulberries</li><li>Smooth Raw Chocolate</li></ul>
    <p class="claim">NO ARTIFICIAL ADDITIVES OR PRESERVATIVES</p>
    <div class="footer-rule"></div>
    <div class="badge badge-organic" role="img" aria-label="Organic certification badge"></div>
    <div class="badge badge-vegan" role="img" aria-label="Vegan certification badge"></div>
  </section>

  <section class="label col-right row-3">
    <div class="brand">VERIDANO</div>
    <div class="title">ZIPPY</div>
    <div class="subtitle is-goji-soft">GOJI</div>
    <div class="divider"></div>
    <p class="blurb">Wonderfully nourishing organic goji berries wrapped in smooth raw chocolate for a bright afternoon lift</p>
    <ul class="ingredients"><li>Organic Goji Berries</li><li>Smooth Raw Chocolate</li></ul>
    <p class="claim">NO ARTIFICIAL ADDITIVES OR PRESERVATIVES</p>
    <div class="footer-rule"></div>
    <div class="badge badge-organic" role="img" aria-label="Organic certification badge"></div>
    <div class="badge badge-vegan" role="img" aria-label="Vegan certification badge"></div>
  </section>

</body>
</html>
```